TA BRAMLEY BUSINESS CARD DESIGN PROJECT

We need to utilize our logo that was expertly created on PixelHarbor and now need to match this with a business card design.

```html
<!DOCTYPE html>
<html lang="en">
<head>
<meta charset="utf-8">
<title>TA Bramley – Business Card</title>
<link href="https://fonts.googleapis.com/css2?family=Montserrat:wght@400;500;700;800&display=swap" rel="stylesheet">
<style>
  :root {
    --stage: #4a4a49;
    --card-black: #181818;
    --paper: #ffffff;
    --brand-blue: #1156ad;
    --ink-light: #f2f2f2;
    --deboss: #2a2a2a;
  }
  * { box-sizing: border-box; margin: 0; padding: 0; }
  html, body { width: 1200px; height: 801px; overflow: hidden; }
  body {
    background: var(--stage);
    font-family: "Montserrat", sans-serif;
    position: relative;
  }
  .card {
    position: absolute;
    left: 340px;
    width: 520px;
    height: 297px;
    background: var(--card-black);
    border-bottom: 3px solid var(--brand-blue);
    overflow: hidden;
    box-shadow: 0 14px 30px rgba(0,0,0,.45);
  }
  .card--front { top: 80px; }
  .card--back { top: 424px; }

  .front-shape { position: absolute; inset: 0; width: 100%; height: 100%; }

  .front-brand {
    position: absolute;
    left: 26px;
    top: 130px;
    width: 170px;
    display: flex;
    align-items: center;
    gap: 8px;
    color: var(--brand-blue);
    font-weight: 800;
    font-size: 21px;
    letter-spacing: 1px;
    white-space: nowrap;
  }
  .front-brand .mark-dot {
    width: 12px; height: 12px; border-radius: 50%;
    background: var(--brand-blue); flex: none;
  }

  .corner-tab {
    position: absolute;
    right: 0; top: 0;
    width: 54px; height: 28px;
    background: var(--brand-blue);
  }

  .contact {
    position: absolute;
    right: 26px;
    top: 44px;
    text-align: right;
    color: var(--ink-light);
  }
  .contact__name {
    color: var(--brand-blue);
    font-weight: 700;
    font-size: 21px;
    letter-spacing: .5px;
  }
  .contact__role { font-size: 13px; margin-top: 2px; }
  .contact__lines { list-style: none; margin-top: 20px; font-size: 13px; line-height: 1.5; }
  .contact__lines li { display: flex; align-items: center; justify-content: flex-end; gap: 8px; }
  .contact__lines svg { width: 11px; height: 11px; fill: var(--brand-blue); flex: none; }
  .contact__address { margin-top: 18px; font-size: 13px; line-height: 1.45; padding-right: 19px; }

  .back-brand {
    position: absolute;
    inset: 0;
    display: flex;
    align-items: center;
    justify-content: center;
    gap: 14px;
    color: var(--deboss);
    font-weight: 800;
    font-size: 50px;
    letter-spacing: 6px;
  }
  .back-brand .mark-dot {
    width: 26px; height: 26px; border-radius: 50%;
    background: var(--deboss);
  }
</style>
</head>
<body>

  <section class="card card--front" aria-label="Business card front">
    <svg class="front-shape" viewBox="0 0 520 297" preserveAspectRatio="none" aria-hidden="true">
      <path d="M0 0 H190 C225 0 238 30 236 80 C233 140 222 190 232 230 C240 262 250 285 262 297 H0 Z" fill="#ffffff"/>
      <path d="M200 4 C236 14 246 44 244 84 C241 144 230 190 240 230 C247 258 256 280 268 294"
            fill="none" stroke="#1156ad" stroke-width="6" stroke-linecap="round"/>
    </svg>

    <div class="front-brand"><span class="mark-dot"></span>TA BRAMLEY</div>

    <div class="corner-tab"></div>

    <div class="contact">
      <p class="contact__name">DANA WHITFIELD</p>
      <p class="contact__role">Managing Director</p>
      <ul class="contact__lines">
        <li>123 456 789
          <svg viewBox="0 0 24 24"><path d="M6.6 10.8a15.1 15.1 0 0 0 6.6 6.6l2.2-2.2a1 1 0 0 1 1-.25 11.4 11.4 0 0 0 3.6.57 1 1 0 0 1 1 1V20a1 1 0 0 1-1 1A17 17 0 0 1 3 4a1 1 0 0 1 1-1h3.5a1 1 0 0 1 1 1 11.4 11.4 0 0 0 .57 3.6 1 1 0 0 1-.25 1z"/></svg>
        </li>
        <li>hello@tabramley.com
          <svg viewBox="0 0 24 24"><path d="M2 5h20v14H2z M2 5l10 8 10-8" /></svg>
        </li>
        <li>www.tabramley.com
          <svg viewBox="0 0 24 24"><circle cx="12" cy="12" r="10"/></svg>
        </li>
      </ul>
      <p class="contact__address">Your address, City<br>State, Zip 1234</p>
    </div>
  </section>

  <section class="card card--back" aria-label="Business card back">
    <div class="back-brand"><span class="mark-dot"></span>TA BRAMLEY</div>
  </section>

</body>
</html>
```